Roofing Contractor business card redesign

I want to redesign my business card with a fresh, eye catching concept

Target Market(s)

Residential Roofing Clients, potential employees, and subcontractors.

Industry/Entity Type

Business

Colors

Designer to choose colors to be used in the design.

Requirements
Nice to have
• I just want something that's more pleasing to the eye. You can use a combination of either / or of my logos.

```html
<!DOCTYPE html>
<html lang="en">
<head>
<meta charset="utf-8">
<title>Fair Hands Builders – Business Card</title>
<link rel="stylesheet" href="https://fonts.googleapis.com/css2?family=Work+Sans:wght@400;700;800&display=swap">
<style>
  :root {
    --brand-brown: #4a1510;
    --brand-orange: #f4821f;
    --card-white: #ffffff;
    --text-dark: #3a3330;
    --backdrop: #2e2e2e;
    --font-main: "Work Sans", Arial, sans-serif;
  }
  * { margin: 0; padding: 0; box-sizing: border-box; }
  html, body {
    width: 1200px; height: 930px; overflow: hidden;
    background: var(--backdrop);
    font-family: var(--font-main);
  }
  .stage { position: relative; width: 1200px; height: 930px; }

  .card {
    position: absolute; left: 278px; width: 644px; height: 368px;
    border-radius: 24px; overflow: hidden;
  }
  .card--front { top: 76px; background: var(--card-white); }
  .card--back { top: 486px; background: var(--brand-orange); }

  /* front */
  .front-brand {
    position: absolute; top: 36px; left: 0; width: 100%;
    display: flex; flex-direction: column; align-items: center; gap: 12px;
  }
  .front-brand__dot {
    width: 96px; height: 96px; border-radius: 50%;
    background: var(--brand-brown);
  }
  .front-brand__name {
    font-weight: 800; font-size: 22px; color: var(--brand-brown);
    white-space: nowrap;
  }
  .divider {
    position: absolute; top: 228px; left: 36px; right: 37px;
    height: 1px; background: var(--brand-orange);
  }
  .contact {
    position: absolute; top: 248px; left: 36px;
    list-style: none; font-size: 17px; color: var(--text-dark);
  }
  .contact li { display: flex; align-items: center; height: 20px; white-space: nowrap; }
  .contact svg { width: 12px; height: 12px; margin-right: 13px; fill: var(--brand-orange); }
  .person {
    position: absolute; top: 242px; right: 37px; text-align: right;
    color: var(--text-dark); white-space: nowrap;
  }
  .person__name { font-size: 29px; color: var(--brand-orange); line-height: 1.1; }
  .person__role { font-size: 17px; line-height: 20px; }
  .address-band {
    position: absolute; left: 0; right: 0; top: 334px; height: 26px;
    background: var(--brand-brown); color: #fff;
    font-size: 17px; text-align: center; line-height: 26px; white-space: nowrap;
  }
  .accent-strip {
    position: absolute; left: 0; right: 0; top: 360px; height: 8px;
    background: var(--brand-orange);
  }

  /* back */
  .back-brand {
    position: absolute; inset: 0;
    display: flex; align-items: center; justify-content: center; gap: 20px;
    color: var(--brand-brown);
  }
  .back-brand__dot {
    width: 72px; height: 72px; border-radius: 50%;
    background: var(--brand-brown); flex: none;
  }
  .back-brand__name {
    font-weight: 800; font-size: 40px; white-space: nowrap;
  }
</style>
</head>
<body>
<main class="stage">

  <section class="card card--front">
    <div class="front-brand">
      <div class="front-brand__dot"></div>
      <div class="front-brand__name">Fair Hands Builders, Inc.</div>
    </div>

    <div class="divider"></div>

    <ul class="contact">
      <li>
        <svg viewBox="0 0 24 24"><path d="M6.6 10.8a15 15 0 0 0 6.6 6.6l2.2-2.2c.3-.3.7-.4 1-.2 1.1.4 2.3.6 3.6.6.6 0 1 .4 1 1V20c0 .6-.4 1-1 1A17 17 0 0 1 3 4c0-.6.4-1 1-1h3.5c.6 0 1 .4 1 1 0 1.3.2 2.5.6 3.6.1.3 0 .7-.2 1z"/></svg>
        (555) 310-2840
      </li>
      <li>
        <svg viewBox="0 0 24 24"><path d="M7 1h10a2 2 0 0 1 2 2v18a2 2 0 0 1-2 2H7a2 2 0 0 1-2-2V3a2 2 0 0 1 2-2zm0 3v14h10V4zm5 15.5a1 1 0 1 0 0 2 1 1 0 0 0 0-2z"/></svg>
        (555) 618-9027
      </li>
      <li>
        <svg viewBox="0 0 24 24"><path d="M2 5h20v14H2zm2 2v.5l8 5 8-5V7zm0 2.8V17h16V9.8l-8 5z"/></svg>
        sam@fairhandsbuild.com
      </li>
    </ul>

    <div class="person">
      <div class="person__name">Sam Harlow</div>
      <div class="person__role">Keller Certified Roof Inspector</div>
      <div class="person__role">Licensed Property Adjuster</div>
    </div>

    <div class="address-band">4410 Cedar Ridge Lane Suite 110 Austin, TX 78701</div>
    <div class="accent-strip"></div>
  </section>

  <section class="card card--back">
    <div class="back-brand">
      <span class="back-brand__dot"></span>
      <span class="back-brand__name">Fair Hands Builders, Inc.</span>
    </div>
  </section>

</main>
</body>
</html>
```